Computer consultant business card

Bexil Software is a newly started computer consulting company. It's a small one-man company that provides mostly Vornix applications but also websites in collaboration with designers. I'm running this company on the side of full time university studies.

I want the final design to be clean and memorable. Be creative! :)

Some inspiration:
http://www.pixelmarta.com/design/48317
http://www.pixelmarta.com/design/2739164/business-card-design-by-frostlynk
http://www.pixelmarta.com/design/604281/business-card-design-by-koralind-vestrabanu

See attachment for my company logo.
Updates

I would like to thank everyone for submitting! I'll need a couple of days to review and ultimately select a design.

Target Market(s)

Non-technical entrepreneurs and small companies.

Industry/Entity Type

University

Requirements
Must have
• My company logo.
In any way, both colors from my logo.
First- and last name, e-mail and phone number.
Double-sided design.
Nice to have
• Something creative with the symbol in my logo

```html
<!DOCTYPE html>
<html lang="en">
<head>
<meta charset="utf-8">
<title>Bexil Software — Business Card</title>
<link href="https://fonts.googleapis.com/css2?family=Source+Sans+3:wght@400;600&display=swap" rel="stylesheet">
<style>
  :root {
    --backdrop: #7a3416;
    --brand-blue: #4472b9;
    --brand-blue-light: #8fa3d8;
    --brand-blue-glow: #c4cdef;
    --ink-dark: #231f20;
    --ink-grey: #6d6e71;
    --paper: #ffffff;
  }
  * { margin: 0; padding: 0; box-sizing: border-box; }
  html, body {
    width: 1200px;
    height: 789px;
    overflow: hidden;
    background: var(--backdrop);
    font-family: "Source Sans 3", "Myriad Pro", Arial, sans-serif;
  }
  .canvas {
    position: relative;
    width: 1200px;
    height: 789px;
  }
  .card {
    position: absolute;
    width: 281px;
    height: 495px;
    box-shadow: 2px 3px 6px rgba(0, 0, 0, 0.45);
    overflow: hidden;
  }
  /* Front side: blue */
  .card--front {
    left: 284px;
    top: 153px;
    background: var(--brand-blue);
  }
  .front-glow {
    position: absolute;
    left: 0;
    top: 30px;
    width: 281px;
    height: 400px;
    background: radial-gradient(circle at 50% 62%, var(--brand-blue-glow) 0%, var(--brand-blue-light) 38%, rgba(143,163,216,0.55) 62%, rgba(68,114,185,0) 80%);
  }
  .front-mark {
    position: absolute;
    left: 103px;
    top: 212px;
    width: 76px;
    height: 76px;
    border-radius: 50%;
    background: var(--brand-blue);
  }
  .front-url {
    position: absolute;
    left: 0;
    right: 0;
    top: 469px;
    text-align: center;
    color: var(--paper);
    font-size: 13.5px;
    letter-spacing: 0.1px;
  }
  /* Back side: white */
  .card--back {
    left: 655px;
    top: 158px;
    width: 279px;
    height: 493px;
    background: var(--paper);
  }
  .brand {
    position: absolute;
    left: 0;
    right: 0;
    top: 88px;
    display: flex;
    align-items: center;
    justify-content: center;
    gap: 12px;
  }
  .brand-dot {
    width: 46px;
    height: 46px;
    border-radius: 50%;
    background: var(--brand-blue);
  }
  .brand-name {
    font-size: 44px;
    font-weight: 600;
    color: var(--ink-dark);
    line-height: 1;
    letter-spacing: 0.5px;
  }
  .person {
    position: absolute;
    left: 0;
    right: 0;
    top: 263px;
    text-align: center;
    font-size: 14.5px;
    line-height: 19px;
  }
  .person-name { color: var(--brand-blue); }
  .person-role { color: var(--ink-grey); }
  .contacts {
    position: absolute;
    left: 0;
    right: 0;
    top: 421px;
    list-style: none;
    text-align: center;
    font-size: 13.5px;
    line-height: 17px;
    color: var(--ink-grey);
  }
  .contacts li {
    display: flex;
    align-items: center;
    justify-content: center;
    gap: 4px;
  }
  .contacts svg {
    width: 12px;
    height: 12px;
    fill: none;
    stroke: var(--brand-blue);
    stroke-width: 1.4;
  }
</style>
</head>
<body>
<main class="canvas">
  <section class="card card--front" aria-label="Business card front">
    <div class="front-glow"></div>
    <div class="front-mark"></div>
    <p class="front-url">www.yourdomain.com</p>
  </section>

  <section class="card card--back" aria-label="Business card back">
    <div class="brand">
      <span class="brand-dot"></span>
      <span class="brand-name">bexil</span>
    </div>
    <div class="person">
      <p class="person-name">Your Name</p>
      <p class="person-role">Designation</p>
    </div>
    <ul class="contacts">
      <li>
        <svg viewBox="0 0 12 12" aria-hidden="true"><circle cx="6" cy="6" r="5"/><path d="M4 3.5c0 2.5 1.5 4.5 4 5"/></svg>
        <span>00-123-4567</span>
      </li>
      <li>
        <svg viewBox="0 0 12 12" aria-hidden="true"><rect x="1" y="5" width="10" height="5"/><rect x="3" y="1.5" width="6" height="3.5"/></svg>
        <span>00-123-4567</span>
      </li>
      <li>
        <svg viewBox="0 0 12 12" aria-hidden="true"><rect x="1" y="2.5" width="10" height="7"/><path d="M1 2.5l5 4 5-4"/></svg>
        <span>name@yourdomain.com</span>
      </li>
    </ul>
  </section>
</main>
</body>
</html>
```